KALEIDOVANTRA FLOOR CATALOGUE for SPC FLOOR

PROJECT BRIEF – KALEIDOVANTRA CATALOG DESIGN
1. Project Overview
Project Title: KALEIDOVANTRA Catalog Design
Objective: To create a visually engaging and emotionally connected product catalog that reflects the unique personality The catalog must combine emotional storytelling with practical product presentation.
2. Brand Concept
KALEIDOVANTRA is a modern, playful, and colorful brand offering high-quality vinyl flooring. The brand is built 3. Collection Overview
KALEIDOVANTRA 5.0
- Hero: Parrot
- Sense: Sight
- Color: Fresh green (#95BF7C)
- Mood: Accessible, youthful, colorful
KALEIDOVANTRA 6.0
- Hero: Dolphin
- Sense: Hearing
- Color: Aqua blue (#69B0E6)
- Mood: Calm, precise, fluid
KALEIDOVANTRA 7.0
- Hero: Galapagos Tortoise
- Sense: Touch
- Color: Ruby red (#E3344F)
- Mood: Solid, premium, safe
4. Design Objectives
- Integrate hero animals clearly and consistently into each collection section
- Use collection colors as a key visual navigation tool (backgrounds, accents, headers)
- Emphasize the sensory identity of each collection with visual or iconographic references to sight, sound, and touch
- Include room for both emotional storytelling and product specifications
- Communicate the LINK & LAY system: all decors available in plank and herringbone formats
5. Visual Style Guidelines
- Typography: Montserrat for headers, Lato for body text
- Layout: modern, clean, consistent grid structure
- Icons: custom-designed line icons for Eye (Sight), Ear (Hearing), Hand (Touch)
- Use illustration or stylized graphic style for animal heroes
- Maintain visual balance between lifestyle/emotion and technical information
6. Deliverables
- Full product catalog layout (A4, print and digital ready)
- Three cover spread layouts (one per collection)
- Icons for sensory experience and product features
- Visual integration of dual format concept (plank + herringbone)
- Consistent styling of all pages, typography, color codes, and image placementsAll details in brief in PDF and some photos like LOGO, already existing materials
Target Market(s)
Europe
Industry/Entity Type
Flooring
Requirements
Must have
- combaine product -SPC Floor with Hero for each collection - animals and with senses - one for each collection.

```html
<!DOCTYPE html>
<html lang="en">
<head>
<meta charset="utf-8">
<title>KALEIDOVANTRA SPC Flooring Catalog</title>
<link rel="stylesheet" href="https://fonts.googleapis.com/css2?family=Montserrat:wght@500;700;800&family=Lato:ital,wght@0,300;0,400;0,700;1,400&display=swap">
<style>
:root{
  --navy:#0f1a2c;
  --navy-deep:#0a1220;
  --aqua:#69b0e6;
  --aqua-light:#8ec0ea;
  --aqua-pale:#a9cff0;
  --ruby:#e3344f;
  --green:#95bf7c;
  --gold:#e8b54a;
  --violet:#7b6fd6;
  --white:#ffffff;
  --ink:#13243d;
  --stage:#d7d8da;
}
*{box-sizing:border-box;margin:0;padding:0}
html,body{width:1037px;height:1200px;overflow:hidden}
body{background:var(--stage);position:relative;font-family:'Lato',sans-serif;color:var(--ink)}

/* ---------- cover ---------- */
.cover{position:absolute;left:328px;top:24px;width:380px;height:537px;
  background:radial-gradient(circle at 50% 55%,#16284a 0%,var(--navy) 55%,var(--navy-deep) 100%);
  color:var(--white);text-align:center;overflow:hidden}
.brand{font-family:'Montserrat',sans-serif;font-weight:700;letter-spacing:3px;color:var(--white)}
.cover .brand{margin-top:34px;font-size:16px}
.brand-sub{font-family:'Montserrat',sans-serif;font-weight:700;font-size:8.5px;letter-spacing:1px;margin-top:3px}
.catalog-tag{display:inline-block;margin-top:8px;border:1.5px solid var(--ruby);padding:3px 0 3px 10px;
  font-family:'Montserrat',sans-serif;font-weight:700;font-size:14px;letter-spacing:12px}
.catalog-tag span:nth-child(1){color:var(--ruby)}
.catalog-tag span:nth-child(2){color:var(--gold)}
.catalog-tag span:nth-child(3){color:var(--green)}
.catalog-tag span:nth-child(4){color:var(--violet)}
.catalog-tag span:nth-child(5){color:var(--aqua)}
.catalog-tag span:nth-child(6){color:var(--green)}
.catalog-tag span:nth-child(7){color:var(--ruby)}
.cover-title{font-family:'Montserrat',sans-serif;font-weight:800;font-size:37px;line-height:1;margin-top:12px}
.cover-sub{font-size:11px;margin-top:7px;letter-spacing:.2px}
.cover-heroes{position:absolute;left:30px;top:222px;width:320px;height:290px;border-radius:40%;
  background:
    radial-gradient(ellipse at 28% 28%,#8da5c8 0%,#3d6aa8 22%,transparent 42%),
    radial-gradient(ellipse at 76% 42%,#e0262e 0%,#b0171f 22%,#1f6b3e 38%,transparent 52%),
    radial-gradient(ellipse at 42% 78%,#e8a43a 0%,#b14ba0 20%,#27b6e8 40%,transparent 62%),
    radial-gradient(ellipse at 50% 55%,#1d5c9c 0%,transparent 70%);
  filter:blur(1px)}

/* ---------- spread ---------- */
.spread{position:absolute;left:138px;top:591px;width:760px;height:537px;display:flex}
.page{position:relative;width:380px;height:537px;overflow:hidden;background:var(--aqua-light)}
.page-left{background:linear-gradient(180deg,var(--aqua-pale) 0%,var(--aqua-light) 60%,var(--aqua) 100%)}
.page-header{position:absolute;left:0;top:0;width:380px;height:76px}
.page-header svg{position:absolute;left:0;top:0}
.page-header .brand{position:absolute;left:18px;top:24px;font-size:10px;letter-spacing:2px}
.page-header .brand-sub{position:absolute;left:42px;top:38px;font-size:6px;color:var(--white);margin:0}
.tagline{position:absolute;left:192px;top:12px;font-family:'Montserrat',sans-serif;font-weight:800;
  font-size:16px;line-height:1.1;color:var(--aqua)}
.sense-icon{position:absolute;left:28px;top:92px}
.collection-name{position:absolute;left:28px;top:164px;font-family:'Montserrat',sans-serif;font-weight:800;font-size:16px;color:var(--ink)}
.collection-ver{position:absolute;left:28px;top:186px;font-size:13px;color:var(--ink)}
.spec-list{position:absolute;left:40px;top:214px;list-style:none;font-size:8px;line-height:17px;color:var(--ink)}
.story{position:absolute;left:28px;top:310px;width:165px;font-size:7.5px;line-height:11px;color:var(--ink)}
.hero-photo{position:absolute;left:205px;top:150px;width:175px;height:340px;
  background:radial-gradient(ellipse at 50% 40%,#9ca9bb 0%,#6f86a6 32%,#4d7eb8 58%,transparent 80%)}

.room-photo{position:absolute;left:0;top:0;width:380px;height:200px;
  background:linear-gradient(160deg,#e6ebf1 0%,#b9c6d6 38%,#6d87a8 70%,#58739a 100%)}
.page-right .content{position:absolute;left:0;top:200px;width:380px;height:337px;background:var(--aqua-light)}
.collection-kicker{position:absolute;left:22px;top:226px;font-size:10px;color:var(--white)}
.system{position:absolute;left:22px;top:242px;width:175px;font-size:16px;font-weight:300;line-height:1.25;color:var(--white)}
.format-tab{position:absolute;background:var(--navy);color:var(--white);font-family:'Montserrat',sans-serif;
  font-weight:800;font-size:11px;padding:4px 12px;letter-spacing:.5px}
.tab-plank{left:22px;top:306px}
.tab-herringbone{left:210px;top:214px}
.format-size{position:absolute;font-size:8.5px;color:var(--ink)}
.format-note{position:absolute;font-size:6.5px;line-height:9px;color:var(--ink);width:150px}
.features{position:absolute;left:0;top:392px;width:380px;display:flex;justify-content:space-around;padding:0 18px}
.feature{width:100px;text-align:center;font-family:'Montserrat',sans-serif;font-weight:700;font-size:8px;color:var(--ink)}
.feature svg{display:block;margin:0 auto 6px}
.page-footer{position:absolute;left:0;bottom:0;width:380px;height:34px;background:var(--navy);
  color:var(--white);font-size:9px;text-align:center;line-height:34px}
</style>
</head>
<body>

<section class="cover" aria-label="Catalog cover">
  <div class="brand">KALEIDOVANTRA</div>
  <div class="brand-sub">SPC FLOORING</div>
  <div class="catalog-tag"><span>C</span><span>A</span><span>T</span><span>A</span><span>L</span><span>O</span><span>G</span></div>
  <h1 class="cover-title">THE FLOOR<br>YOU CAN FEEL</h1>
  <p class="cover-sub">3 collections. 3 senses. 1 story of transformation.</p>
  <div class="cover-heroes" role="img" aria-label="Collection heroes: a dolphin in water, a scarlet parrot and a colourful sea turtle on a glowing blue background"></div>
</section>

<section class="spread" aria-label="Collection 6.0 spread">
  <article class="page page-left">
    <header class="page-header">
      <svg width="380" height="76" viewBox="0 0 380 76" aria-hidden="true">
        <path d="M0 0H380V56H188Q178 56 176 70Q174 56 164 56H0Z" fill="var(--navy)"/>
      </svg>
      <div class="brand">KALEIDOVANTRA</div>
      <div class="brand-sub">SPC FLOORING</div>
      <div class="tagline">Feel the Color.<br>Enjoy the Form.</div>
    </header>

    <svg class="sense-icon" width="70" height="60" viewBox="0 0 70 60" aria-label="Hearing icon" role="img">
      <g fill="none" stroke="var(--white)" stroke-width="3" stroke-linecap="round">
        <path d="M10 22C10 10 20 4 28 4C38 4 45 11 45 21C45 30 36 32 35 40C34 48 30 54 23 54C17 54 14 50 14 46"/>
        <path d="M20 22C20 15 24 12 28 12C33 12 36 16 36 20C36 25 31 26 29 30"/>
        <path d="M52 16Q56 21 52 26M58 12Q64 21 58 30"/>
      </g>
    </svg>
    <h2 class="collection-name">KALEIDOVANTRA</h2>
    <div class="collection-ver">6.0 (Dolphin)</div>
    <ul class="spec-list">
      <li>HERO: Dolphin</li>
      <li>SENSE: Hearing</li>
      <li>COLOR: Aqua blue (#69B0E6)</li>
      <li>MOOD: Calm, precise, fluid</li>
    </ul>
    <p class="story">Lorem ipsum dolor sit amet, consectetuer adipiscing elit, sed diam nonummy nibh euismod tincidunt ut laoreet dolore magna aliquam erat volutpat. Ut wisi enim ad minim veniam, quis nostrud exerci tation ullamcorper suscipit lobortis nisl ut aliquip ex ea commodo consequat. Duis autem vel eum iriure dolor in hendrerit in vulputate velit esse molestie consequat, vel illum dolore eu feugiat nulla facilisis at vero eros et accumsan et iusto odio dignissim qui blandit praesent luptatum zzril delenit augue duis dolore te feugait nulla facilisi.</p>
    <div class="hero-photo" role="img" aria-label="Dolphin rising from calm blue water"></div>
  </article>

  <article class="page page-right">
    <div class="room-photo" role="img" aria-label="Interior with blue-grey herringbone and plank floor, white vanity and grey sofa"></div>
    <div class="content"></div>
    <div class="collection-kicker">6.0 (Dolphin)</div>
    <div class="system">LINK &amp; LAY system-<br>Your style. Your choice.</div>

    <div class="format-tab tab-plank">PLANK</div>
    <div class="format-size" style="left:22px;top:330px">Standard plank 1220x180 mm</div>
    <p class="format-note" style="left:22px;top:344px">Lorem ipsum dolor sit amet, consectetuer adipiscing elit, sed diam nonummy nibh euismod tincidunt ut laoreet dolore magna aliquam erat volutpat.</p>

    <div class="format-tab tab-herringbone">HERRINGBONE</div>
    <div class="format-size" style="left:210px;top:238px">Herringbone 610x123 mm</div>
    <p class="format-note" style="left:210px;top:252px">Lorem ipsum dolor sit amet, consectetuer adipiscing elit, sed diam nonummy nibh euismod tincidunt ut laoreet dolore magna aliquam erat volutpat.</p>

    <div class="features">
      <div class="feature">
        <svg width="44" height="44" viewBox="0 0 44 44" aria-hidden="true"><g fill="none" stroke="var(--white)" stroke-width="1.5"><circle cx="22" cy="22" r="20"/><path d="M22 10C18 16 16 19 16 22A6 6 0 0 0 28 22C28 19 26 16 22 10Z"/><path d="M12 31H32M14 34H30"/></g></svg>
        Water Resistance
      </div>
      <div class="feature">
        <svg width="44" height="44" viewBox="0 0 44 44" aria-hidden="true"><g fill="none" stroke="var(--white)" stroke-width="1.5"><circle cx="22" cy="22" r="20"/><path d="M11 26L22 20L33 26L22 32Z"/><path d="M17 14H20L24 11V19L20 16H17Z"/></g></svg>
        Acoustic Comfort
      </div>
      <div class="feature">
        <svg width="44" height="44" viewBox="0 0 44 44" aria-hidden="true"><g fill="none" stroke="var(--white)" stroke-width="1.5"><circle cx="22" cy="22" r="20"/><path d="M14 13H28L30 17H14Z"/><path d="M20 17V29H24V17"/><path d="M12 32H32"/></g></svg>
        Durability
      </div>
    </div>
    <footer class="page-footer">Feels light. Looks expressive.</footer>
  </article>
</section>

</body>
</html>
```